Chimney Service company needs new business card design

We need a updated business card with our new logo added. We provide a full range of chimney services throughout Vermont and New Hampshire. The business card will be one sided and color. Attached is our current business card another document showing all the information we would like on the card.
We dont like a lot of flashy colors.... here is a link to our website to get an idea of our branding www.flueguardianvt.example

Target Market(s)

homeowners

Industry/Entity Type

Business

Contact Information for Business Card

See attached sheet for content.

Font styles to use
Serif
Sans Serif

Requirements
Must have
• all information provided on separate sheet
Should not have
• Additional information that may clogg up design

```html
<!DOCTYPE html>
<html lang="en">
<head>
<meta charset="utf-8">
<title>Flue Guardian – Business Card</title>
<link href="https://fonts.googleapis.com/css2?family=Marcellus&display=swap" rel="stylesheet">
<style>
  :root {
    --backdrop: #e9e6e1;
    --card-dark: #2a2a2c;
    --card-mid: #3c3c3f;
    --ink-light: #f2f2f2;
    --ink-soft: #cfcfd1;
    --accent-red: #9e1b1f;
    --edge-grey: #c9ccce;
  }
  * { box-sizing: border-box; margin: 0; padding: 0; }
  html, body {
    width: 1200px; height: 1022px; overflow: hidden;
    background: var(--backdrop);
  }
  .stage {
    width: 1200px; height: 1022px;
    display: flex; align-items: center; justify-content: center;
  }
  .business-card {
    position: relative;
    width: 1050px; height: 600px;
    background: linear-gradient(160deg, var(--card-mid) 0%, var(--card-dark) 55%, #222224 100%);
    font-family: "Marcellus", Georgia, serif;
    color: var(--ink-light);
    overflow: hidden;
    box-shadow: 0 10px 30px rgba(0,0,0,.25);
  }
  .brand {
    position: absolute; left: 70px; top: 110px;
    display: flex; align-items: center; gap: 26px;
  }
  .brand-square {
    width: 110px; height: 110px;
    border: 8px solid var(--ink-light);
    flex: none;
  }
  .brand-name {
    font-size: 64px; letter-spacing: 4px; line-height: 1;
    text-transform: uppercase; white-space: nowrap;
  }
  .brand-rule {
    position: absolute; left: 206px; top: 200px;
    width: 690px; height: 3px; background: var(--ink-light);
  }
  .brand-year {
    position: absolute; left: 206px; top: 218px; width: 690px;
    display: flex; align-items: center; gap: 18px;
    font-size: 30px; letter-spacing: 5px; color: var(--ink-soft);
  }
  .brand-year::before, .brand-year::after {
    content: ""; flex: 1; height: 2px; background: var(--ink-soft);
  }
  .brand-year::before { flex: 0 0 130px; }
  .services {
    position: absolute; left: 70px; top: 330px;
    list-style: none; font-size: 25px; letter-spacing: 1.5px;
    line-height: 40px; text-transform: uppercase;
  }
  .services li::before, .services .dot::before {
    content: ""; display: inline-block; width: 10px; height: 10px;
    border-radius: 50%; background: var(--accent-red);
    margin-right: 14px; vertical-align: middle;
  }
  .services .dot { margin-left: 12px; }
  .contact {
    position: absolute; right: 60px; top: 420px;
    list-style: none; font-size: 25px; line-height: 40px; letter-spacing: .5px;
  }
  .contact li { display: flex; align-items: center; gap: 14px; }
  .contact svg { width: 20px; height: 20px; flex: none; }
  .card-edge {
    position: absolute; left: 0; bottom: 0; width: 100%; height: 30px;
    display: flex;
  }
  .card-edge .edge-grey { flex: 0 0 740px; background: var(--edge-grey); }
  .card-edge .edge-red { flex: 1; background: var(--accent-red); }
</style>
</head>
<body>
<main class="stage">
  <article class="business-card">
    <div class="brand">
      <span class="brand-square"></span>
      <span class="brand-name">Flue Guardian</span>
    </div>
    <div class="brand-rule"></div>
    <div class="brand-year">INC 1989</div>

    <ul class="services">
      <li>Full Masonry Services</li>
      <li>Historic Chimney Restoration</li>
      <li>Stainless Steel Liners</li>
      <li>VCSA Certified Chimney Sweep</li>
      <li>Fully Insured<span class="dot"></span>Free Estimates</li>
    </ul>

    <ul class="contact">
      <li>
        <svg viewBox="0 0 20 20" aria-hidden="true"><path d="M5 2l3 4-2 2c1 2.5 3.5 5 6 6l2-2 4 3-2 3C9 17 3 11 2 4z" fill="#9e1b1f"/></svg>
        802-555-0147
      </li>
      <li>
        <svg viewBox="0 0 20 20" aria-hidden="true"><rect x="2" y="4" width="16" height="12" fill="none" stroke="#9e1b1f" stroke-width="2"/><path d="M2 4l8 7 8-7" fill="none" stroke="#9e1b1f" stroke-width="2"/></svg>
        info@flueguardianvt.example
      </li>
      <li>
        <svg viewBox="0 0 20 20" aria-hidden="true"><circle cx="10" cy="10" r="8" fill="none" stroke="#9e1b1f" stroke-width="2"/><path d="M2 10h16M10 2c-4 5-4 11 0 16M10 2c4 5 4 11 0 16" fill="none" stroke="#9e1b1f" stroke-width="1.5"/></svg>
        www.flueguardianvt.example
      </li>
    </ul>

    <div class="card-edge">
      <span class="edge-grey"></span>
      <span class="edge-red"></span>
    </div>
  </article>
</main>
</body>
</html>
```